Business Cards for a law firm

Business cards for our law firm. Use our silhoette logo and OAK PARTNERS - check our website (www.oakpartners.example)

Contact Information for Business Card

our silhouette logo, OAK PARTNERS, 800-555-0147, Dorian Pemberton, dorian@oakpartners.example

Requirements
Must have
• our silhouette logo, OAK PARTNERS, 800-555-0147, Dorian Pemberton, dorian@oakpartners.example

```html
<!DOCTYPE html>
<html lang="en">
<head>
<meta charset="utf-8">
<title>Oak Partners – Business Cards</title>
<link href="https://fonts.googleapis.com/css2?family=Cinzel:wght@500;600&family=Open+Sans:wght@700&family=Montserrat:wght@400;500&display=swap" rel="stylesheet">
<style>
  :root {
    --stage: #e7e4df;
    --card-white: #ffffff;
    --navy: #233369;
    --navy-deep: #1c2a5c;
    --navy-soft: #34478a;
    --ink: #1e1e24;
    --white: #ffffff;
  }
  * { margin: 0; padding: 0; box-sizing: border-box; }
  html, body {
    width: 900px; height: 1200px; overflow: hidden;
    background: var(--stage);
  }
  .canvas { position: relative; width: 900px; height: 1200px; }

  .card {
    position: absolute;
    border-radius: 22px;
    overflow: hidden;
    box-shadow: 0 10px 24px rgba(0,0,0,0.25);
  }
  .card--front { left: 80px; top: 131px; width: 742px; height: 441px; background: var(--card-white); }
  .card--back  { left: 78px; top: 638px; width: 744px; height: 440px; background: var(--navy); }

  /* logo area: invented name stands where the mark sits */
  .logo-area {
    position: absolute; left: 20px; top: 34px; width: 270px; height: 400px;
    display: flex; flex-direction: column; align-items: center; justify-content: center; gap: 18px;
  }
  .logo-area__square { width: 64px; height: 64px; background: var(--navy); }
  .logo-area__name {
    font-family: "Cinzel", serif; font-weight: 600; font-size: 22px;
    letter-spacing: 2px; color: var(--navy);
  }
  .back-mark {
    position: absolute; left: 40px; top: 120px; width: 200px; height: 200px;
    background: var(--navy-soft); opacity: 0.45;
  }

  .firm-name {
    position: absolute; font-family: "Cinzel", serif; font-weight: 600;
    letter-spacing: 2.5px; white-space: nowrap;
  }
  .card--front .firm-name { left: 363px; top: 80px; font-size: 28px; color: var(--navy); }
  .card--back .firm-name { left: 315px; top: 335px; font-size: 33px; color: var(--white); font-weight: 500; }

  .person { position: absolute; left: 361px; top: 176px; }
  .person__name { font-family: "Open Sans", sans-serif; font-weight: 700; font-size: 26px; color: var(--navy); line-height: 1.1; }
  .person__role { font-family: "Montserrat", sans-serif; font-size: 16px; color: var(--ink); margin-top: 4px; }

  .address {
    position: absolute; left: 360px; top: 245px;
    font-family: "Montserrat", sans-serif; font-size: 16px; line-height: 21px; color: var(--ink); font-style: normal;
  }
  .contact-list { position: absolute; left: 360px; top: 302px; list-style: none; }
  .contact-list li {
    display: flex; align-items: center; gap: 9px; height: 28.5px;
    font-family: "Montserrat", sans-serif; font-size: 16px; color: var(--ink);
  }
  .contact-list svg { width: 15px; height: 15px; fill: var(--navy); flex: none; }
</style>
</head>
<body>
<main class="canvas">
  <section class="card card--front" aria-label="Business card front">
    <div class="logo-area">
      <span class="logo-area__square"></span>
      <span class="logo-area__name">OAK PARTNERS</span>
    </div>
    <h1 class="firm-name">OAK PARTNERS</h1>
    <div class="person">
      <p class="person__name">Dorian Pemberton</p>
      <p class="person__role">Lawyer</p>
    </div>
    <address class="address">418 Maple Grove Ave, #112<br>Lakeview, OH 43210</address>
    <ul class="contact-list">
      <li>
        <svg viewBox="0 0 24 24" aria-hidden="true"><path d="M6.6 10.8a15.2 15.2 0 0 0 6.6 6.6l2.2-2.2a1 1 0 0 1 1-.25 11.4 11.4 0 0 0 3.6.57 1 1 0 0 1 1 1V20a1 1 0 0 1-1 1A17 17 0 0 1 3 4a1 1 0 0 1 1-1h3.5a1 1 0 0 1 1 1c0 1.25.2 2.45.57 3.57a1 1 0 0 1-.25 1z"/></svg>
        800-555-0147
      </li>
      <li>
        <svg viewBox="0 0 24 24" aria-hidden="true"><path d="M2 5h20v2l-10 6L2 7z M2 9l10 6 10-6v10H2z"/></svg>
        dorian@oakpartners.example
      </li>
      <li>
        <svg viewBox="0 0 24 24" aria-hidden="true"><circle cx="12" cy="12" r="10"/><path d="M7 7c2 1 2 3 4 3s1 3 3 3-1 4-1 6c-2 0-3-3-4-5S6 11 7 7zm9-2c0 2 2 3 3 3 0 2-2 2-3 1s-2-2 0-4z" fill="#fff"/></svg>
        www.oakpartners.example
      </li>
    </ul>
  </section>

  <section class="card card--back" aria-label="Business card back">
    <div class="back-mark" role="img" aria-label="Faint firm mark area"></div>
    <h2 class="firm-name">OAK PARTNERS</h2>
  </section>
</main>
</body>
</html>
```